Business Card Design

New business card design

Target Market(s)

Residential & Commercial Property Managers

Industry/Entity Type

Plumbing Services

Contact Information for Business Card

Name - Rowan Keddle, title - Director, Phone Number - 0431 286 517, email - rowan@tbk-plumbing.com.au, Company ABN - 73 215 904 386,

Font styles to use
Sans Serif

Colors
0054AA
0677BA
7BADD7
CADEEF
E8F1F8

```html
<!DOCTYPE html>
<html lang="en">
<head>
<meta charset="utf-8">
<title>TBK Plumbing Services – Business Card</title>
<link rel="stylesheet" href="https://fonts.googleapis.com/css2?family=Montserrat:wght@400;500;700&display=swap">
<style>
  :root {
    --page: #e9ebed;
    --card: #ffffff;
    --navy: #1e252c;
    --aqua: #2ca6e0;
    --ink-soft: #6a5f58;
    --white: #ffffff;
  }
  * { box-sizing: border-box; margin: 0; padding: 0; }
  html, body { width: 1200px; height: 900px; overflow: hidden; }
  body {
    background: var(--page);
    font-family: "Montserrat", Arial, sans-serif;
    display: flex;
    flex-direction: column;
    align-items: center;
    justify-content: center;
    gap: 20px;
  }
  .card {
    position: relative;
    width: 700px;
    height: 400px;
    background: var(--card);
    border-radius: 30px;
    overflow: hidden;
    box-shadow: 0 6px 18px rgba(0,0,0,0.12);
  }
  .card-shapes { position: absolute; inset: 0; width: 100%; height: 100%; }
  .shape-navy { fill: var(--navy); }
  .shape-aqua { fill: var(--aqua); }

  .holder { position: absolute; left: 48px; top: 34px; color: var(--white); }
  .holder-name { font-size: 27px; font-weight: 700; letter-spacing: 0.5px; white-space: nowrap; }
  .holder-title { font-size: 17px; font-weight: 400; margin-top: 2px; }

  .contact {
    position: absolute; left: 40px; top: 236px;
    color: var(--white); font-size: 17px; font-weight: 400; line-height: 1.3;
  }
  .contact-abn { margin-bottom: 8px; }
  .contact-row { display: flex; align-items: center; gap: 10px; white-space: nowrap; }
  .contact-icon { width: 17px; height: 17px; flex: none; }

  .brand {
    position: absolute;
    display: flex; flex-direction: column; align-items: center;
    color: var(--navy); font-weight: 500;
  }
  .brand-front { left: 385px; top: 120px; width: 290px; }
  .brand-back { left: 0; right: 0; top: 110px; }
  .brand-name {
    display: flex; align-items: center; gap: 14px;
    font-size: 96px; line-height: 1; letter-spacing: 4px;
  }
  .brand-back .brand-name { font-size: 128px; }
  .brand-dot { width: 22px; height: 22px; border-radius: 50%; background: var(--aqua); }
  .brand-tagline {
    font-size: 14px; letter-spacing: 7px; margin-top: 14px; white-space: nowrap;
  }
  .brand-back .brand-tagline { font-size: 20px; letter-spacing: 16px; }
</style>
</head>
<body>

  <section class="card card-back" aria-label="Business card, logo side">
    <div class="brand brand-back">
      <div class="brand-name">tbk<span class="brand-dot"></span></div>
      <div class="brand-tagline">plumbing services</div>
    </div>
  </section>

  <section class="card card-front" aria-label="Business card, contact side">
    <svg class="card-shapes" viewBox="0 0 700 400" preserveAspectRatio="none" aria-hidden="true">
      <path class="shape-navy" d="M0 0 H430 C360 4 325 60 285 108 C248 152 218 178 165 178 H0 Z"/>
      <path class="shape-aqua" d="M0 188 H250 C305 188 330 235 350 300 C368 360 388 392 415 400 H0 Z"/>
    </svg>

    <div class="holder">
      <div class="holder-name">Rowan Keddle</div>
      <div class="holder-title">Director</div>
    </div>

    <div class="contact">
      <div class="contact-abn">Company ABN -<br>73 215 904 386</div>
      <div class="contact-row">
        <svg class="contact-icon" viewBox="0 0 24 24" aria-hidden="true">
          <path fill="#fff" d="M6.6 10.8a15.1 15.1 0 0 0 6.6 6.6l2.2-2.2c.3-.3.7-.4 1-.2 1.1.4 2.3.6 3.6.6.6 0 1 .4 1 1V20c0 .6-.4 1-1 1A17 17 0 0 1 3 4c0-.6.4-1 1-1h3.5c.6 0 1 .4 1 1 0 1.3.2 2.5.6 3.6.1.3 0 .7-.2 1z"/>
        </svg>
        <span>0431 286 517</span>
      </div>
      <div class="contact-row">
        <svg class="contact-icon" viewBox="0 0 24 24" aria-hidden="true">
          <path fill="none" stroke="#fff" stroke-width="2" d="M3 9l9-6 9 6v11H3z M3 9l9 6 9-6"/>
        </svg>
        <span>rowan@tbk-plumbing.com.au</span>
      </div>
    </div>

    <div class="brand brand-front">
      <div class="brand-name">tbk<span class="brand-dot"></span></div>
      <div class="brand-tagline">plumbing services</div>
    </div>
  </section>

</body>
</html>
```